Brochure for a website accessibility report

This brochure is related to a report that www.qelvantrix.org sell. The report shows the results of an automated audit of a websites accessibility. It shows details of issues found with screen shots, examples of code and provides remediation advice.

The brochure will be a pdf 8.5 inches by 11 inches. It can be anywhere from 6 to 10 pages.

The FlintVue™ name itself should be “Bree Serif” font. The fonts, styles, colors and sizes are up to you.

The images used and logo of the Office of Digital Reachworks and K7P logo are upload

We highlighted in blue page extracts from the report we sell. Do not use the blue highlight, it is merely there to show you where the specific examples of the report we sell are vs the other content in the report. The areas in blue which show the content from the actual report should be shown as an extract of the actual page of the report. You have flexibility to change the layout and the way the content look.

The red square callouts over the blue content are callouts that describe the specific page extracts. We used it as a red callout only so that you would be able to see it. You should change the specific location, look and feel of the callout to be appropriate

Target Market(s)

Marketing and Technical people

Industry/Entity Type

Information Technology

Font styles to use
Sans Serif

Colors

Designer to choose colors to be used in the design.

Requirements
Should not have
• wheelchairs, images of blind people

```html
<!DOCTYPE html>
<html lang="en">
<head>
<meta charset="utf-8">
<title>FlintVue™ Report Extract – Link Text Issue</title>
<link rel="stylesheet" href="https://fonts.googleapis.com/css2?family=Roboto:wght@400;500&family=PT+Serif&display=swap">
<style>
  :root {
    --page-bg: #ffffff;
    --navy: #0c3a5c;
    --panel-top: #3390cb;
    --panel-bottom: #2d85c0;
    --white: #ffffff;
    --code-yellow: #f3cf3c;
    --link-cyan: #3fdcd6;
    --callout: #f6cd3c;
    --callout-text: #1f4a6e;
    --snippet-bg: #e9e9e9;
    --snippet-text: #1e2a38;
  }
  * { margin: 0; padding: 0; box-sizing: border-box; }
  html, body { width: 928px; height: 1200px; overflow: hidden; background: var(--page-bg); }
  body { position: relative; font-family: "Roboto", sans-serif; color: var(--white); }

  .report-sheet {
    position: absolute; left: 53px; top: 0; width: 822px; height: 1146px;
    background: var(--navy); border-radius: 0 0 80px 80px;
    box-shadow: 0 10px 30px rgba(0,0,0,0.18);
  }
  .advice { position: absolute; left: 52px; top: 48px; width: 730px; }
  .advice h3 { font-weight: 500; font-size: 16px; margin-bottom: 6px; }
  .advice p { font-size: 16px; line-height: 19px; font-weight: 400; }
  .advice .block { margin-bottom: 16px; }
  .code-line { font-family: "PT Serif", serif; color: var(--code-yellow); font-size: 15.5px; margin-left: 37px; margin-bottom: 4px; }
  .indent { margin-left: 36px; }
  .reading a { display: block; color: var(--link-cyan); text-decoration: none; font-size: 17px; line-height: 20px; margin-left: 42px; }

  .example-panel {
    position: absolute; left: 30px; top: 413px; width: 759px; height: 699px;
    border-radius: 36px; overflow: hidden;
    background: linear-gradient(var(--panel-top) 0 352px, var(--panel-bottom) 352px);
  }
  .example-title { position: absolute; left: 21px; top: 17px; font-size: 17.5px; letter-spacing: 0.1px; }
  .example-title strong { font-weight: 500; margin-right: 8px; }
  .example-title span { font-weight: 400; }
  .page-capture {
    position: absolute; left: 22px; top: 55px; width: 309px; height: 247px;
    background: linear-gradient(180deg, #f4f4f4 0 14%, #c08a5c 14% 60%, #e2ddd6 60% 72%, #8a7466 72%);
    border: 2px solid #ffffff;
  }
  .specific { position: absolute; left: 22px; top: 410px; width: 720px; }
  .specific h4 { font-size: 17px; font-weight: 500; margin-bottom: 5px; }
  .specific p { font-size: 15.5px; line-height: 22.5px; font-weight: 400; }
  .specific .hl { color: var(--code-yellow); }
  .specific .serif { font-family: "PT Serif", serif; }
  .snippet-label { position: absolute; left: 22px; top: 536px; font-size: 17px; font-weight: 500; }
  .snippet {
    position: absolute; left: 22px; top: 567px; width: 718px; height: 86px;
    background: var(--snippet-bg); color: var(--snippet-text);
    font-family: "PT Serif", serif; font-size: 14.5px; line-height: 18px; padding: 17px 20px;
  }

  .callout { position: absolute; left: 466px; top: 678px; width: 298px; height: 144px; }
  .callout svg { position: absolute; left: 0; top: 0; }
  .callout p {
    position: absolute; left: 32px; top: 29px; width: 238px;
    color: var(--callout-text); font-size: 15.5px; line-height: 23px; text-align: justify;
    text-align-last: left;
  }
</style>
</head>
<body>
  <section class="report-sheet">
    <div class="advice">
      <div class="block">
        <h3>General Remediation Advice:</h3>
        <p>When dealing with images directly contained within links with link text, don't use the same text in the image alt text as the link text.</p>
      </div>
      <div class="block">
        <h3>Before:</h3>
        <p class="code-line">&lt;a href="products.html"&gt;&lt;img src="products.gif" alt="Products page"/&gt;Products page&lt;/a&gt;</p>
        <p class="indent">This leads to a "stutter" as screen readers will read "Products page" twice: once for the image and once for the link. Replace the alt text with "".</p>
      </div>
      <div class="block">
        <h3>After:</h3>
        <p class="code-line">&lt;a href="products.html"&gt;&lt;img src="icon.gif" alt="" /&gt;Products page&lt;/a&gt;</p>
      </div>
      <div class="block reading">
        <h3>Suggested Reading:</h3>
        <a href="#">Compatible</a>
        <a href="#">Link Purpose (In Context)</a>
      </div>
    </div>

    <div class="example-panel">
      <p class="example-title"><strong>EXAMPLE 1 OF 7:</strong><span>HTTPS://WWW.NORVENDIA.ORG/OUTREACH/CIVIC/ACCESS-ES/</span></p>
      <div class="page-capture" role="img" aria-label="Screenshot of the audited Spanish-language web page with news photos and headlines"></div>

      <div class="specific">
        <h4>SPECIFIC ISSUES:</h4>
        <p>Image links should not duplicate link-text with the 'ALT' attribute.</p>
        <p>Found link text ' <span class="hl serif">MÁS INFORMACIÓN</span> ' within ALT of <span class="hl">&lt;IMG&gt; Tag</span></p>
        <p class="hl">src='http://www.norvendia.org/outreach/civic/accessfr/wp-content/uploads/sites&nbsp; /28/2015/10/ico_en.gif'.</p>
      </div>

      <p class="snippet-label">CODE SNIPPET</p>
      <div class="snippet">&lt;IMG STYLE="VERTICAL-ALIGN: BASELINE" SRC="HTTP://WWW.NORVENDIA.ORG/OUTREACH/CIVIC/ACCESSFR /WPCONTENT/UPLOADS/SITES /28/2015/10/ICO_EN.GIF" ALT="M&amp;#193;S INFORMACI&amp;#211;N"&gt;</div>
    </div>

    <div class="callout">
      <svg width="298" height="144" viewBox="0 0 298 144" aria-hidden="true">
        <rect x="0" y="0" width="298" height="117" rx="16" fill="var(--callout)"/>
        <path d="M38 116 L54 143 L70 116 Z" fill="var(--callout)"/>
      </svg>
      <p>THE SPECIFIC ISSUE DISCOVERED PROVIDES DETAIL NEEDED TO UNDERSTAND THE ISSUE</p>
    </div>
  </section>
</body>
</html>
```